Computer consultant business card

Bexil Software is a newly started computer consulting company. It's a small one-man company that provides mostly Vornix applications but also websites in collaboration with designers. I'm running this company on the side of full time university studies.

I want the final design to be clean and memorable. Be creative! :)

Some inspiration:
http://www.pixelmarta.com/design/48317
http://www.pixelmarta.com/design/2739164/business-card-design-by-frostlynk
http://www.pixelmarta.com/design/604281/business-card-design-by-koralind-vestrabanu

See attachment for my company logo.
Updates

I would like to thank everyone for submitting! I'll need a couple of days to review and ultimately select a design.

Target Market(s)

Non-technical entrepreneurs and small companies.

Industry/Entity Type

University

Requirements
Must have
• My company logo.
In any way, both colors from my logo.
First- and last name, e-mail and phone number.
Double-sided design.
Nice to have
• Something creative with the symbol in my logo

```html
<!DOCTYPE html>
<html lang="en">
<head>
<meta charset="utf-8">
<title>Bexil Software — Business Card</title>
<link rel="stylesheet" href="https://fonts.googleapis.com/css2?family=Exo+2:wght@400;500;700&display=swap">
<style>
  :root {
    --brand-blue: #2a7de1;
    --brand-dark: #333232;
    --card-white: #ffffff;
    --backdrop: #ececec;
    --faint-grey: #ececec;
    --faint-blue: #e6eefb;
    --text-dark: #262626;
  }
  html, body {
    margin: 0;
    padding: 0;
    width: 1200px;
    height: 784px;
    overflow: hidden;
    background: var(--backdrop);
    font-family: "Exo 2", sans-serif;
  }
  .canvas {
    position: relative;
    width: 1200px;
    height: 784px;
  }
  .card {
    position: absolute;
    width: 540px;
    height: 310px;
    background: var(--card-white);
    box-shadow: 0 2px 10px rgba(0,0,0,0.12);
    overflow: hidden;
  }
  .card--front { left: 50px; top: 90px; }
  .card--back  { left: 610px; top: 384px; }

  .card__band {
    position: absolute;
    top: 0;
    bottom: 0;
    width: 90px;
    border-radius: 45px 45px 0 0;
  }
  .card--front .card__band { right: 70px; top: 20px; background: var(--faint-grey); }
  .card--back  .card__band { left: 40px; top: -40px; background: var(--faint-blue); border-radius: 0 0 45px 45px; }

  .wordmark {
    position: absolute;
    display: flex;
    align-items: center;
    gap: 16px;
    color: var(--brand-dark);
    font-weight: 500;
    letter-spacing: 1px;
  }
  .wordmark__dot {
    border-radius: 50%;
    background: var(--brand-blue);
  }
  .card--front .wordmark { left: 44px; top: 46px; font-size: 68px; }
  .card--front .wordmark__dot { width: 58px; height: 58px; }
  .card--back .wordmark { left: 150px; top: 108px; font-size: 74px; }
  .card--back .wordmark__dot { width: 64px; height: 64px; }

  .contact {
    position: absolute;
    left: 58px;
    top: 188px;
    color: var(--text-dark);
    font-size: 15px;
  }
  .contact__name {
    margin: 0 0 18px;
    font-size: 17px;
  }
  .contact__first {
    color: var(--brand-blue);
    font-weight: 700;
  }
  .contact__row {
    display: flex;
    align-items: center;
    gap: 8px;
    margin: 0 0 8px;
  }
  .contact__row svg { width: 11px; height: 11px; fill: var(--brand-blue); }
  .contact__address { margin: 14px 0 0 0; }
</style>
</head>
<body>
<main class="canvas">
  <section class="card card--front" aria-label="Card front">
    <div class="card__band"></div>
    <div class="wordmark">
      <span class="wordmark__dot"></span>
      <span class="wordmark__name">bexil</span>
    </div>
    <div class="contact">
      <p class="contact__name"><span class="contact__first">First Name,</span> Last Name</p>
      <p class="contact__row">
        <svg viewBox="0 0 12 12" aria-hidden="true"><path d="M2.5 0.5 L4.5 0.5 L5.5 3.5 L4 4.6 Q5 7 7.4 8 L8.5 6.5 L11.5 7.5 L11.5 9.5 Q11.5 11.5 9.5 11.5 Q0.5 11 0.5 2.5 Q0.5 0.5 2.5 0.5 Z"/></svg>
        <span>0987 654321</span>
      </p>
      <p class="contact__row">
        <svg viewBox="0 0 12 12" aria-hidden="true"><path d="M0.5 2.5 H11.5 V10 H0.5 Z M1 3 L6 7 L11 3" /></svg>
        <span>info@bexilsoft.com</span>
      </p>
      <p class="contact__address">00, Complex name, City, State 0042</p>
    </div>
  </section>

  <section class="card card--back" aria-label="Card back">
    <div class="card__band"></div>
    <div class="wordmark">
      <span class="wordmark__dot"></span>
      <span class="wordmark__name">bexil</span>
    </div>
  </section>
</main>
</body>
</html>
```